RUVO WARE LTD

Advertisement to get more schools:
use website https://www.ruvo-ware.co.uk for logos etc.
ICT Service Level Agreements for as little as £2000 per year
Unlimited Remote, phone and email support
Unlimited Call outs included
90% fix time within 30 minutes of ticket submission
Extra support during Scolvar inspections
GDPR service included

Education

```html
<!DOCTYPE html>
<html lang="en">
<head>
<meta charset="utf-8">
<title>RUVO WARE LTD – ICT SLA Agreements</title>
<link rel="stylesheet" href="https://fonts.googleapis.com/css2?family=Fira+Sans:wght@400;600;700&display=swap">
<style>
  :root {
    --orange: #f07c45;
    --orange-soft: rgba(240, 124, 69, 0.92);
    --black: #0d0d0d;
    --blue: #0a72b8;
    --blue-deep: #0b4f80;
    --navy-text: #164c7e;
    --pale: #edf1f4;
    --divider: #d3d9de;
    --footer: #1b1b1b;
    --white: #ffffff;
  }
  * { margin: 0; padding: 0; box-sizing: border-box; }
  html, body { width: 832px; height: 1200px; overflow: hidden; background: var(--white); }
  body { font-family: "Fira Sans", Arial, sans-serif; }
  .advert { position: relative; width: 832px; height: 1200px; overflow: hidden; }

  /* Hero */
  .hero { position: absolute; left: 0; top: 0; width: 832px; height: 433px; overflow: hidden; }
  .hero-photo { position: absolute; inset: 0;
    background: linear-gradient(120deg, #c9ccd0 0%, #8e8a88 30%, #6b3a36 50%, #a9adb2 75%, #d6d8da 100%); }
  .offer-disc { position: absolute; left: 458px; top: -31px; width: 416px; height: 416px;
    border-radius: 50%; background: var(--black); }
  .brand { position: absolute; left: 534px; top: 40px; width: 250px; display: flex; align-items: center; gap: 10px; }
  .brand-mark { width: 16px; height: 16px; background: var(--orange); }
  .brand-name { color: var(--orange); font-weight: 700; font-size: 31px; letter-spacing: 1px; white-space: nowrap; }
  .offer { position: absolute; left: 500px; width: 320px; text-align: center; color: var(--white); font-weight: 700; }
  .offer-line { font-size: 23px; line-height: 35px; }
  .offer-lead { top: 131px; }
  .offer-price { top: 208px; font-size: 68px; line-height: 80px; color: var(--orange); }
  .offer-unit { top: 292px; }

  /* Feature band */
  .band { position: absolute; left: 0; top: 433px; width: 832px; height: 120px; display: flex; }
  .band-cell { height: 100%; display: flex; align-items: center; color: var(--white); font-size: 21px; line-height: 33px; }
  .band-cell.left { width: 416px; background: var(--blue); padding-left: 23px; }
  .band-cell.right { width: 416px; background: var(--blue-deep); padding-left: 45px; }
  .band-icon { width: 63px; height: 63px; border-radius: 8px; background: var(--orange);
    display: flex; align-items: center; justify-content: center; margin-right: 22px; flex: none; }

  /* Promise */
  .promise { position: absolute; left: 0; top: 553px; width: 832px; height: 333px; overflow: hidden; }
  .promise-photo { position: absolute; inset: 0;
    background: linear-gradient(100deg, #3a2e27 0%, #6a5a4d 35%, #9a8f86 55%, #4a3a30 80%, #2a2019 100%); }
  .promise-disc { position: absolute; left: 164px; top: -80px; width: 488px; height: 488px;
    border-radius: 50%; background: var(--orange-soft); }
  .promise-rule { position: absolute; left: 226px; width: 364px; height: 3px; background: var(--white); }
  .promise-rule.top { top: 84px; }
  .promise-rule.bottom { top: 250px; }
  .promise-text { position: absolute; left: 176px; top: 102px; width: 464px; text-align: center;
    color: var(--white); font-weight: 700; font-size: 31px; line-height: 43.5px; }

  /* Benefits */
  .benefits { position: absolute; left: 0; top: 886px; width: 832px; height: 239px; background: var(--pale); display: flex; }
  .benefit { width: 416px; height: 100%; position: relative; text-align: center; color: var(--navy-text);
    font-size: 21px; line-height: 34px; }
  .benefit-icon { position: absolute; top: 30px; left: 50%; transform: translateX(-50%); }
  .benefit-label { position: absolute; top: 146px; left: 0; width: 100%; }
  .benefit.left { width: 411px; }
  .benefits-divider { width: 2px; height: 191px; margin-top: 17px; background: var(--divider); }
  .benefit.right { width: 419px; }

  /* Footer */
  .footer { position: absolute; left: 0; top: 1125px; width: 832px; height: 75px; background: var(--footer);
    color: var(--white); font-size: 16px; display: flex; align-items: center; justify-content: center; }
</style>
</head>
<body>
<main class="advert">
  <section class="hero">
    <div class="hero-photo" role="img" aria-label="Photo of a pupil wearing a virtual reality headset in a classroom"></div>
    <div class="offer-disc"></div>
    <div class="brand"><span class="brand-mark"></span><span class="brand-name">RUVO WARE</span></div>
    <div class="offer offer-lead offer-line">ICT SLA AGREEMENTS<br>FOR AS LITTLE AS</div>
    <div class="offer offer-price">£2000</div>
    <div class="offer offer-unit offer-line">PER YEAR</div>
  </section>

  <section class="band">
    <div class="band-cell left">
      <span class="band-icon">
        <svg width="40" height="36" viewBox="0 0 40 36" aria-hidden="true">
          <path d="M4 3h22a3 3 0 0 1 3 3v12a3 3 0 0 1-3 3H13l-7 6v-6H4a3 3 0 0 1-3-3V6a3 3 0 0 1 3-3z" fill="#fff"/>
          <path d="M31 11h5a3 3 0 0 1 3 3v11a3 3 0 0 1-3 3h-2v5l-6-5H18a3 3 0 0 1-3-3v-1" fill="none" stroke="#fff" stroke-width="2.5"/>
          <rect x="7" y="9" width="16" height="2.5" rx="1.2" fill="#f07c45"/>
          <rect x="7" y="14" width="11" height="2.5" rx="1.2" fill="#f07c45"/>
        </svg>
      </span>
      <span>UNLIMITED REMOTE,<br>PHONE AND EMAIL SUPPORT</span>
    </div>
    <div class="band-cell right">
      <span class="band-icon">
        <svg width="38" height="38" viewBox="0 0 24 24" aria-hidden="true">
          <path d="M6.6 10.8a15 15 0 0 0 6.6 6.6l2.2-2.2a1 1 0 0 1 1-.25 11.4 11.4 0 0 0 3.6.57 1 1 0 0 1 1 1V20a1 1 0 0 1-1 1A17 17 0 0 1 3 4a1 1 0 0 1 1-1h3.5a1 1 0 0 1 1 1c0 1.25.2 2.45.57 3.6a1 1 0 0 1-.25 1z" fill="#fff"/>
          <path d="M14 10l5-5M15 5h4v4" fill="none" stroke="#fff" stroke-width="1.6" stroke-linecap="round"/>
        </svg>
      </span>
      <span>UNLIMITED CALL OUTS<br>INCLUDED</span>
    </div>
  </section>

  <section class="promise">
    <div class="promise-photo" role="img" aria-label="Blurred photo of a hand holding a phone in front of a laptop showing the support portal"></div>
    <div class="promise-disc"></div>
    <div class="promise-rule top"></div>
    <p class="promise-text">90% FIX TIME WITHIN<br>30 MINUTES OF TICKET<br>SUBMISSION</p>
    <div class="promise-rule bottom"></div>
  </section>

  <section class="benefits">
    <div class="benefit left">
      <svg class="benefit-icon" width="100" height="100" viewBox="0 0 100 100" aria-hidden="true" fill="none" stroke="#f07c45" stroke-width="3" stroke-linecap="round">
        <path d="M28 42a22 22 0 0 1 44 0"/>
        <rect x="22" y="38" width="8" height="14" rx="3"/>
        <rect x="70" y="38" width="8" height="14" rx="3"/>
        <path d="M74 52v4a6 6 0 0 1-6 6h-10"/>
        <rect x="24" y="64" width="52" height="28" rx="3"/>
        <path d="M14 93h72"/>
        <circle cx="50" cy="78" r="3"/>
        <path d="M12 30v4M12 40v4M88 20v4M88 30v4"/>
      </svg>
      <p class="benefit-label">EXTRA SUPPORT DURING<br>SCOLVAR INSPECTIONS</p>
    </div>
    <div class="benefits-divider"></div>
    <div class="benefit right">
      <svg class="benefit-icon" width="96" height="82" viewBox="0 0 96 82" aria-hidden="true" fill="none" stroke="#f07c45" stroke-width="5" stroke-linejoin="round" stroke-linecap="round">
        <path d="M6 12a6 6 0 0 1 6-6h22l8 9h42a6 6 0 0 1 6 6v49a6 6 0 0 1-6 6H12a6 6 0 0 1-6-6z"/>
        <path d="M34 46l10 10 18-19"/>
      </svg>
      <p class="benefit-label">GDPR SERVICE<br>INCLUDED</p>
    </div>
  </section>

  <footer class="footer">Copyright © 2022 All Rights Reserved</footer>
</main>
</body>
</html>
```